Advertising company unique advertising platform

we need a logo design for a new company based in Australia Melbourne. We develop innovated advertising platform where consumer can use this platform to get regular discount, as business owner they can use this platform for free advertisement. Payment for this advertisement platform only payable every two weeks, when I generate revenue for their business

Industry/Entity Type

Advertising

Contact Information for Business Card

Dale Morven | Co-Founder |Managing Director
Suite 718 240 Wattlebrook Lane Melbourne Vic 3000

ABN 38 614 207 923
Tel: +61 0487 259 318 | Email: dale.morven@plivorantu.com

Font styles to use
Decorative
Script

Requirements
Must have
• Try few different design and some round corner business card
Should not have
• One round corner business card...try 4 different colour background not only black, make sure two side is designed. Be creative so imagine you are giving this to a client make sure has wow factor, if you can also try one design with engrave like all the logo, words look 3d feel
• The word Advertising Platform use attached file font

```html
<!DOCTYPE html>
<html lang="en">
<head>
<meta charset="utf-8">
<title>Nexvale Market – Business Card</title>
<link rel="stylesheet" href="https://fonts.googleapis.com/css2?family=Source+Sans+3:wght@400;600;700&display=swap">
<style>
  :root{
    --backdrop:#e6e6e6;
    --card-dark:#1c1c1c;
    --orange-deep:#e2452a;
    --orange-mid:#f07a22;
    --amber:#f6c23a;
    --accent-red:#f0502e;
    --accent-teal:#22c7a9;
    --accent-blue:#2aa7e0;
    --ink-light:#e9e9e9;
    --white:#ffffff;
  }
  *{margin:0;padding:0;box-sizing:border-box;}
  html,body{width:1200px;height:840px;overflow:hidden;}
  body{
    background:var(--backdrop);
    font-family:"Source Sans 3",sans-serif;
    display:flex;align-items:center;justify-content:center;gap:30px;
  }
  .card{
    position:relative;width:560px;height:320px;border-radius:22px;overflow:hidden;
    box-shadow:0 6px 18px rgba(0,0,0,.18);
  }
  /* Front */
  .card--front{
    background:radial-gradient(ellipse at 50% 42%,var(--amber) 0%,var(--orange-mid) 45%,var(--orange-deep) 100%);
    display:flex;flex-direction:column;align-items:center;justify-content:center;
  }
  .brand{display:flex;align-items:center;gap:12px;}
  .brand__dot{width:34px;height:34px;border-radius:50%;}
  .brand__name{font-weight:700;font-size:38px;letter-spacing:.5px;}
  .card--front .brand__dot{background:var(--white);}
  .card--front .brand__name{color:var(--white);}
  .website{
    margin-top:26px;color:var(--white);font-size:13px;letter-spacing:4px;opacity:.9;
  }
  /* Back */
  .card--back{background:var(--card-dark);color:var(--ink-light);}
  .contact{position:absolute;left:30px;top:34px;font-size:14px;line-height:1.28;}
  .contact__name{color:var(--accent-red);font-weight:700;font-size:16px;text-transform:uppercase;}
  .contact__role{color:var(--accent-teal);font-weight:600;font-size:15px;text-transform:uppercase;}
  .contact__label{color:var(--accent-red);font-weight:700;}
  .contact__phone{margin-top:2px;}
  .divider{position:absolute;left:30px;right:22px;top:188px;height:1px;background:var(--ink-light);opacity:.8;}
  .card--back .brand{position:absolute;right:34px;top:92px;}
  .card--back .brand__dot{background:var(--orange-mid);}
  .card--back .brand__name{color:var(--orange-mid);font-size:32px;}
  .address{position:absolute;right:30px;top:204px;text-align:right;font-size:15px;line-height:1.3;}
  .edge-band{position:absolute;left:0;right:0;bottom:0;height:14px;}
</style>
</head>
<body>
  <section class="card card--front" aria-label="Card front">
    <div class="brand">
      <span class="brand__dot"></span>
      <span class="brand__name">Nexvale Market</span>
    </div>
    <p class="website">www.plivorantu.com</p>
  </section>

  <section class="card card--back" aria-label="Card back">
    <div class="contact">
      <p class="contact__name">Dale Morven</p>
      <p class="contact__role">Co-Founder</p>
      <p class="contact__role">Managing Director</p>
      <p class="contact__phone"><span class="contact__label">P :</span> +61 0487 259 318</p>
      <p>dale.morven@plivorantu.com</p>
      <p>Plivorantu</p>
      <p>ABN 38 614 207 923</p>
    </div>
    <div class="brand">
      <span class="brand__dot"></span>
      <span class="brand__name">Nexvale Market</span>
    </div>
    <div class="divider"></div>
    <address class="address" style="font-style:normal">
      Suite 718 240<br>Wattlebrook Lane<br>Melbourne Vic 3000
    </address>
    <svg class="edge-band" viewBox="0 0 560 14" preserveAspectRatio="none" aria-hidden="true">
      <defs>
        <linearGradient id="bandWarm" x1="0" x2="1" y1="0" y2="0">
          <stop offset="0" stop-color="#e2452a"/>
          <stop offset=".45" stop-color="#f6c23a"/>
          <stop offset="1" stop-color="#e2452a"/>
        </linearGradient>
      </defs>
      <rect x="0" y="0" width="560" height="3" fill="#2aa7e0"/>
      <rect x="0" y="3" width="560" height="11" fill="url(#bandWarm)"/>
    </svg>
  </section>
</body>
</html>
```